Pepper & Palm Business Card FUN & EXCITING

Here is the Information for the Card:
Jaswinder Bains (Ravi)
E: RaviBains@postlark.com
C: (480) 555-0147
www.PepperPalmLV.com

We don't want traditional Indian cliche, We a playful bold and fun business card.

Files: https://files.cloudvessel.net/share/folders/7TqRmXpZ2vKa9LwBn4YcHd3JsEf6UoGi?usp=share_link

https://files.cloudvessel.net/share/folders/4MzXaQ8rTw2YbNcVk6PsLe5GhJdR3FoU?usp=share_link

Target Market(s)

Las Vegas Local Restaurant

Industry/Entity Type

Indian Restaurant

Contact Information for Business Card

Name, Email, Cell Phone, Company Logo

```html
<!DOCTYPE html>
<html lang="en">
<head>
<meta charset="utf-8">
<title>Pepper &amp; Palm – Business Card</title>
<link rel="stylesheet" href="https://fonts.googleapis.com/css2?family=Anton&family=Oswald:wght@600&family=Yellowtail&family=Playfair+Display:ital@1&display=swap">
<style>
  :root{
    --backdrop:#2b2b2b;
    --cream:#fcf4d9;
    --ink:#111111;
    --pink:#f0306e;
    --teal:#1fa89a;
    --orange:#ea9322;
    --orange-deep:#ef7f2a;
    --green:#2e9a43;
    --mail:#e27aa0;
  }
  *{box-sizing:border-box;margin:0;padding:0}
  html,body{width:1200px;height:689px;overflow:hidden;background:var(--backdrop)}
  .stage{position:relative;width:1200px;height:689px}

  .card{position:absolute;top:190px;width:540px;height:309px;border-radius:22px;overflow:hidden}

  /* back of card */
  .card--back{left:30px;background:linear-gradient(135deg,var(--pink),var(--orange) 50%,var(--teal))}
  .card--back .border-pattern{position:absolute;inset:0}
  .card--back .panel{position:absolute;inset:22px;background:var(--cream);border-radius:26px}
  .back-logo{position:absolute;left:36px;top:28px;font-family:"Anton",sans-serif;color:var(--ink);font-size:54px;line-height:.98;letter-spacing:1px}
  .back-place{position:absolute;left:38px;top:146px;font-family:"Playfair Display",serif;font-style:italic;font-size:14px;color:var(--ink)}
  .tagline{position:absolute;left:38px;top:174px;font-family:"Playfair Display",serif;font-style:italic;font-size:14px;color:var(--ink);white-space:nowrap}
  .back-art{position:absolute;right:30px;top:30px;width:180px;height:160px;border-radius:18px;background:radial-gradient(circle at 45% 45%,#fff 0,#f4dfb8 55%,var(--orange) 100%)}
  .socials{position:absolute;left:0;right:0;bottom:26px;display:flex;justify-content:center;gap:22px;list-style:none}
  .socials li{display:flex;align-items:center;gap:6px;font-family:"Oswald",sans-serif;font-weight:600;font-size:13px;line-height:1;color:var(--ink)}
  .socials .dot{width:14px;height:14px;border-radius:50%}
  .dot--a{background:#3b5a9a}.dot--b{background:#d42a6c}.dot--c{background:#d32323}

  /* front of card */
  .card--front{left:630px;background:var(--cream)}
  .front-band{position:absolute;left:210px;top:0;width:330px;height:170px;background:var(--orange);border-bottom-left-radius:120px}
  .front-name{position:absolute;left:226px;right:24px;top:18px;text-align:right;font-family:"Yellowtail",cursive;font-weight:400;font-size:26px;line-height:1.2;color:var(--ink);white-space:nowrap}
  .front-art{position:absolute;right:22px;top:68px;width:268px;height:210px;border-radius:60px 30px 30px 100px;background:radial-gradient(circle at 40% 40%,#ffffff 0,#f5e4c3 45%,var(--orange-deep) 100%)}
  .front-logo{position:absolute;left:30px;top:112px;font-family:"Anton",sans-serif;font-size:42px;line-height:.98;color:var(--ink)}
  .front-place{position:absolute;left:32px;top:198px;font-family:"Playfair Display",serif;font-style:italic;font-size:12px;color:var(--ink)}
  .contacts{position:absolute;left:30px;bottom:18px;list-style:none}
  .contacts li{display:flex;align-items:center;gap:8px;font-family:"Oswald",sans-serif;font-weight:600;font-size:14px;line-height:1.5;color:var(--ink);white-space:nowrap}
  .contacts .icon{width:16px;height:16px;border-radius:50%;display:flex;align-items:center;justify-content:center;flex:none}
  .icon--phone{background:var(--orange-deep)}.icon--mail{background:var(--mail)}.icon--web{background:var(--green)}
</style>
</head>
<body>
<main class="stage">

  <section class="card card--back">
    <div class="border-pattern" role="img" aria-label="Colourful floral pattern border in pink, orange and teal"></div>
    <div class="panel">
      <div class="back-logo">PEPPER<br>&amp; PALM</div>
      <div class="back-place">Las Vegas, NV</div>
      <p class="tagline">“A match made in heaven”</p>
      <div class="back-art" role="img" aria-label="Cartoon curry bowl and flatbread characters walking together with hearts"></div>
      <ul class="socials">
        <li><span class="dot dot--a"></span>Friendloop</li>
        <li><span class="dot dot--b"></span>Snapgrid</li>
        <li><span class="dot dot--c"></span>Tastecard</li>
      </ul>
    </div>
  </section>

  <section class="card card--front">
    <div class="front-band"></div>
    <h1 class="front-name">Jaswinder Bains (Ravi)</h1>
    <div class="front-art" role="img" aria-label="Cartoon curry bowl pointing ahead beside a walking flatbread character, with hearts and sparkles"></div>
    <div class="front-logo">PEPPER<br>&amp; PALM</div>
    <div class="front-place">Las Vegas, NV</div>
    <ul class="contacts">
      <li><span class="icon icon--phone"><svg width="8" height="11" viewBox="0 0 8 11"><rect x="1" y="0.5" width="6" height="10" rx="1.2" fill="none" stroke="#fff" stroke-width="1.2"/></svg></span>(480) 555-0147</li>
      <li><span class="icon icon--mail"><svg width="10" height="8" viewBox="0 0 10 8"><rect x="0.6" y="0.6" width="8.8" height="6.8" fill="none" stroke="#fff" stroke-width="1.1"/><path d="M0.6 0.6 5 4.4 9.4 0.6" fill="none" stroke="#fff" stroke-width="1.1"/></svg></span>RaviBains@postlark.com</li>
      <li><span class="icon icon--web"><svg width="10" height="10" viewBox="0 0 10 10"><circle cx="5" cy="5" r="4.2" fill="none" stroke="#fff" stroke-width="1.1"/><path d="M0.8 5h8.4M5 0.8c-2.2 2.5-2.2 5.9 0 8.4M5 0.8c2.2 2.5 2.2 5.9 0 8.4" fill="none" stroke="#fff" stroke-width="0.9"/></svg></span>PepperPalmLV.com</li>
    </ul>
  </section>

</main>
</body>
</html>
```